Graphic Design Project

We make rose petal jelly from old fashioned english roses. The jelly is sweet eaten with scones and clotted cream or as a filling in a victoria sandwich, as a topping on ice cream or thick set yogurt.
The image of the product is luxurious and decadent and very english.
We need a design for a label which has a picture of an old fashioned rose (rosa mundi or a compte de chambard) The rose must stand out clearly so the jelly is not confused with other fruit jams. The overall colour of the label should be pink and soft, with white or dark pink writing. The label needs to be fridge proof.

We also need a security strip to fit on the lid of the jar.

We need the following information on the label.
Name of our company-"Meadow Crown"
Name of Product-"Rose Petal Jelly"
Sales pitch-"With whole petals-a taste of summer, delicious on scones, as a filling in sponge cake, as a topping on ice cream or yogurt."
INGREDIENTS: Sugar, water, rose petals, lemon juice, natural jelling agent (agar-agar)
STORAGE: Store in a cool dry place, once opened keep refrigerated and consume within 4 weeks.
BEST BEFORE: See base

200g
Produced by:
MEADOW CROWN
The Larches
Pardew Lane
Newnham
Gloucestershire
GL17 4RX
The label must have room for a bar code. The size of label approx 8-10cm long 5cm wide.
Updates

Hi

Just been looking at the Hartwell and Brace site and the labels they have there have the up market feel I am trying to convey. Hope that helps, its classy but not twee.

Thanks

Thanks for all submissions. I would be grateful if you googled images for 'Colourful and expensive biscuits at Hartwell Brace' The designs on the tins are the image we are trying to create. The colours are quite strong.

Thanks

Target Market(s)

older well off people who visit garden centres

Industry/Entity Type

Security

Requirements
Must have
• All writen info above and picture of old fashioned rose prferably rose a mundi. Luxury feel, very english, to appeal to older market
Pink colour sheme
Should not have
• dark or manly colours

```html
<!DOCTYPE html>
<html lang="en">
<head>
<meta charset="utf-8">
<title>Meadow Crown Rose Petal Jelly Label</title>
<link rel="stylesheet" href="https://fonts.googleapis.com/css2?family=Courgette&family=Sofia&display=swap">
<style>
  :root {
    --page: #ffffff;
    --label: #f2e4a4;
    --script: #c92a5a;
    --title-fill: #e58fc6;
    --title-line: #a8336c;
    --info: #e38acb;
    --code-box: #ffffff;
  }
  html, body {
    margin: 0;
    width: 1200px;
    height: 1200px;
    overflow: hidden;
    background: var(--page);
  }
  .canvas {
    position: relative;
    width: 1200px;
    height: 1200px;
  }
  .label {
    position: absolute;
    left: 34px;
    top: 317px;
    width: 1133px;
    height: 567px;
    background: var(--label);
  }
  .pitch {
    position: absolute;
    margin: 0;
    font-family: "Courgette", cursive;
    font-size: 32px;
    letter-spacing: 2px;
    color: var(--script);
    white-space: nowrap;
    transform: translate(-50%, -50%);
  }
  .pitch--top { left: 490px; top: 46px; }
  .pitch--bottom { left: 513px; top: 528px; }
  .pitch--left { left: 42px; top: 285px; transform: translate(-50%, -50%) rotate(90deg); }
  .pitch--right { left: 1098px; top: 282px; transform: translate(-50%, -50%) rotate(90deg); }

  .brand {
    position: absolute;
    left: 116px;
    top: 84px;
    margin: 0;
    font-family: "Sofia", cursive;
    font-weight: 400;
    font-size: 56px;
    line-height: 1;
    color: var(--title-fill);
    -webkit-text-stroke: 1.2px var(--title-line);
    white-space: nowrap;
  }
  .product {
    position: absolute;
    left: 189px;
    top: 158px;
    margin: 0;
    font-family: "Sofia", cursive;
    font-weight: 400;
    font-size: 36px;
    line-height: 1;
    color: var(--script);
    white-space: nowrap;
  }
  .roses {
    position: absolute;
    left: 74px;
    top: 210px;
    width: 480px;
    height: 300px;
  }
  .info {
    position: absolute;
    left: 675px;
    top: 280px;
    width: 410px;
    transform: translate(-50%, -50%) rotate(-90deg);
    font-family: "Courgette", cursive;
    font-size: 15.5px;
    line-height: 22px;
    color: var(--info);
    text-align: center;
  }
  .info p { margin: 0; white-space: nowrap; }
  .barcode-space {
    position: absolute;
    left: 774px;
    top: 74px;
    width: 284px;
    height: 420px;
    background: var(--code-box);
  }
</style>
</head>
<body>
<div class="canvas">
  <section class="label">
    <p class="pitch pitch--top">with whole petals-a taste of summer,</p>
    <p class="pitch pitch--left">as a filling in sponge cake,</p>
    <p class="pitch pitch--right">delicious on scones,</p>
    <p class="pitch pitch--bottom">as a topping on ice cream or yogurt.</p>

    <h1 class="brand">Meadow Crown</h1>
    <h2 class="product">Rose Petal Jelly</h2>

    <svg class="roses" viewBox="0 0 480 300" role="img" aria-label="Two striped Rosa Mundi roses, a large pink and crimson bloom beside a smaller pale peach bloom">
      <defs>
        <radialGradient id="rose-large" cx="50%" cy="45%" r="55%">
          <stop offset="0%" stop-color="#d62c7a"/>
          <stop offset="60%" stop-color="#e07cbd"/>
          <stop offset="100%" stop-color="#eaa3d2"/>
        </radialGradient>
        <radialGradient id="rose-small" cx="50%" cy="45%" r="55%">
          <stop offset="0%" stop-color="#f08a86"/>
          <stop offset="100%" stop-color="#f9d0c4"/>
        </radialGradient>
      </defs>
      <ellipse cx="377" cy="151" rx="98" ry="102" fill="url(#rose-small)"/>
      <ellipse cx="145" cy="144" rx="143" ry="140" fill="url(#rose-large)"/>
    </svg>

    <div class="info">
      <p>200 g INGREDIENTS: Sugar, water, rose</p>
      <p>petals, lemon juice, natural jelling agent (agar-agar)</p>
      <p>STORAGE: Store in a cool dry place, once opened</p>
      <p>keep refrigerated and consume within 4 weeks.</p>
      <p>BEST BEFORE: See base</p>
      <p>Produced by: MEADOW CROWN</p>
      <p>The Larches, Pardew Lane, Newnham, Gloucestershire</p>
      <p>GL17 4RX</p>
    </div>

    <div class="barcode-space"></div>
  </section>
</div>
</body>
</html>
```